Business card for my new company (Accounting firm)

I need a business card for my new business Brightwell Advisory and Ledger SA. Our services are accounting, tax, audit and financial management. Our customers are small companies, start-ups and new companies. The final design has to show financial security, trust and growth. Please find our logo attached to the business card. Text for the business card: Brightwell Advisory and Ledger SA Tomas Varenholt Director and Founder Certified Accountant Tel. 022 418 57 34 tv@clairevalconseil.ch www.clairevalconseil.ch Rue des Vergières 27 1201 Geneva
Target Market(s)
Our customers are small companies, start-ups and new companies.
Industry/Entity Type
Finance And Accounting
Contact Information for Business Card
Claireval Conseil et Comptes SA
Tomas Varenholt
Directeur et Fondateur
Expert-comptable diplômé
Tél. 022 418 57 34
tv@clairevalconseil.ch
www.clairevalconseil.ch
Rue des Vergières 27
1201 Genève

```html
<!DOCTYPE html>
<html lang="fr">
<head>
<meta charset="utf-8">
<title>Claireval Conseil et Comptes SA – Carte de visite</title>
<link href="https://fonts.googleapis.com/css2?family=Roboto:wght@400;500;700&display=swap" rel="stylesheet">
<style>
  :root {
    --bg: #e9ecef;
    --sky: #31b0e3;
    --navy: #1b6597;
    --white: #ffffff;
    --ink: #3b3f44;
    --soft-ink: #5b6066;
  }
  html, body {
    margin: 0;
    width: 1200px;
    height: 960px;
    overflow: hidden;
    background: var(--bg);
    font-family: "Roboto", Arial, sans-serif;
  }
  .card {
    position: absolute;
    width: 580px;
    height: 330px;
    border-radius: 2px;
    box-shadow: 0 6px 18px rgba(0,0,0,.18);
    overflow: hidden;
  }
  /* back side */
  .card-back {
    left: 90px;
    top: 110px;
    background: var(--sky);
  }
  .card-back .pattern-field {
    position: absolute;
    inset: 0;
    background: linear-gradient(135deg, #35b4e6, #2eaadd);
  }
  .card-back .brand-mark {
    position: absolute;
    right: 34px;
    top: 148px;
    display: flex;
    align-items: center;
    gap: 8px;
    color: var(--white);
    font-weight: 700;
    font-size: 20px;
    letter-spacing: 2px;
  }
  .brand-square {
    width: 14px;
    height: 14px;
    background: currentColor;
  }
  /* front side */
  .card-front {
    left: 530px;
    top: 500px;
    background: var(--white);
  }
  .card-front .swoosh {
    position: absolute;
    inset: 0;
  }
  .person {
    position: absolute;
    left: 30px;
    top: 30px;
    color: var(--white);
  }
  .person-name {
    margin: 0 0 4px;
    font-size: 24px;
    font-weight: 700;
  }
  .person-role {
    margin: 0;
    font-size: 14px;
    line-height: 1.3;
  }
  .brand-lockup {
    position: absolute;
    right: 40px;
    top: 110px;
    text-align: left;
    color: var(--ink);
  }
  .brand-lockup .brand-row {
    display: flex;
    align-items: center;
    gap: 10px;
    font-size: 36px;
    font-weight: 500;
    letter-spacing: 3px;
    line-height: 1;
  }
  .brand-lockup .brand-square {
    width: 20px;
    height: 20px;
    background: var(--navy);
  }
  .brand-lockup .tagline {
    margin-top: 6px;
    font-size: 11px;
    font-weight: 500;
    letter-spacing: 2.6px;
    color: var(--ink);
    padding-left: 30px;
  }
  .contact {
    position: absolute;
    left: 200px;
    top: 190px;
    color: var(--ink);
    font-size: 15px;
    line-height: 1.3;
  }
  .address {
    margin: 0 0 10px;
    font-style: normal;
  }
  .contact-list {
    list-style: none;
    margin: 0;
    padding: 0;
  }
  .contact-list li {
    display: flex;
    align-items: center;
    gap: 8px;
  }
  .contact-list svg {
    width: 13px;
    height: 13px;
    fill: var(--sky);
    flex: none;
  }
</style>
</head>
<body>

<section class="card card-back" aria-label="Verso de la carte">
  <div class="pattern-field" role="img" aria-label="Motif de fond répété aux couleurs de la marque"></div>
  <div class="brand-mark"><span class="brand-square"></span>CLAIREVAL</div>
</section>

<section class="card card-front" aria-label="Recto de la carte">
  <svg class="swoosh" viewBox="0 0 580 330" preserveAspectRatio="none" aria-hidden="true">
    <path d="M0,0 H560 C380,40 110,120 0,255 Z" fill="var(--navy)"/>
    <path d="M560,0 C380,40 110,120 0,255 V290 C120,140 380,45 575,4 Z" fill="var(--sky)"/>
    <path d="M575,4 C380,45 120,140 0,290 V300 C125,150 390,55 578,10 Z" fill="var(--white)"/>
  </svg>

  <div class="person">
    <h1 class="person-name">Tomas Varenholt</h1>
    <p class="person-role">Directeur et Fondateur<br>Expert-comptable diplômé</p>
  </div>

  <div class="brand-lockup">
    <div class="brand-row"><span class="brand-square"></span>CLAIREVAL</div>
    <div class="tagline">CONSEIL ET COMPTES</div>
  </div>

  <div class="contact">
    <address class="address">Rue des Vergières 27<br>1201 Genève</address>
    <ul class="contact-list">
      <li>
        <svg viewBox="0 0 24 24"><path d="M6.6 10.8a15.1 15.1 0 0 0 6.6 6.6l2.2-2.2a1 1 0 0 1 1-.25 11.4 11.4 0 0 0 3.6.57 1 1 0 0 1 1 1V20a1 1 0 0 1-1 1A17 17 0 0 1 3 4a1 1 0 0 1 1-1h3.5a1 1 0 0 1 1 1c0 1.25.2 2.45.57 3.57a1 1 0 0 1-.25 1z"/></svg>
        022 418 57 34
      </li>
      <li>
        <svg viewBox="0 0 24 24"><path d="M2 5h20v14H2z M3.5 6.5 12 13l8.5-6.5" fill="var(--sky)" stroke="#fff" stroke-width="1.5"/></svg>
        tv@clairevalconseil.ch
      </li>
      <li>
        <svg viewBox="0 0 24 24"><circle cx="12" cy="12" r="10"/><path d="M2 12h20M12 2c3 3 3 17 0 20M12 2c-3 3-3 17 0 20" fill="none" stroke="#fff" stroke-width="1.3"/></svg>
        www.clairevalconseil.ch
      </li>
    </ul>
  </div>
</section>

</body>
</html>
```